Card design for orthopaedic surgeons working as The Brightwater Joint Centre

Business cards, letterhead

Colors

Designer to choose colors to be used in the design.

Requirements
Must have
• Late addition.
• Cards letterhead must have logos of
• Crestmoor Lindell College of Surgeons
• Varenwood Bone Health Association
Nice to have
• Back of card to have space for appointment time to be added by hand and some blank space for writing incidental other notes.

```html
<!DOCTYPE html>
<html lang="en">
<head>
<meta charset="utf-8">
<title>The Brightwater Joint Centre – Stationery</title>
<link href="https://fonts.googleapis.com/css2?family=Nunito+Sans:wght@400;600;700&family=Arimo:wght@400;700&display=swap" rel="stylesheet">
<style>
  :root{
    --bg:#e3e3e3;
    --paper:#f5f5f5;
    --blue:#4f9fd8;
    --navy:#123049;
    --ink:#222;
    --line:#7fb6e0;
    --badge-gold:#c9a86a;
    --badge-red:#b8463a;
  }
  *{box-sizing:border-box;margin:0;padding:0}
  html,body{width:1200px;height:1200px;overflow:hidden}
  body{background:var(--bg);position:relative;font-family:"Nunito Sans",sans-serif;color:var(--navy)}
  .sheet{position:absolute;background:var(--paper);box-shadow:2px 3px 8px rgba(0,0,0,.3);overflow:hidden}
  .letterhead{left:57px;top:84px;width:728px;height:1028px}
  .brand-name{position:absolute;color:var(--blue);font-weight:600;white-space:nowrap;letter-spacing:-.2px}
  .letterhead .brand-name{left:50px;top:80px;font-size:25px}
  .practice-info{position:absolute;right:52px;top:48px;text-align:right;line-height:1.25}
  .doctor{color:var(--blue);font-weight:600;font-size:12.5px}
  .doctor .quals{font-size:10px;font-weight:700}
  .contact{font-size:11px;color:var(--navy);line-height:1.25;letter-spacing:.3px}
  .practice-info .contact{margin-top:6px}
  .contact div{display:flex;justify-content:flex-end;align-items:center;gap:4px}
  .icon{width:9px;height:9px;flex:none}
  .letter{position:absolute;left:50px;top:238px;width:626px;font-family:"Arimo",sans-serif;color:var(--ink);font-size:11px;line-height:14.7px}
  .letter p{margin-bottom:14.5px;text-align:justify}
  .letter .date{margin-bottom:14px}
  .letter .recipient{margin-bottom:28px;text-align:left}
  .letter .salutation{font-weight:700;margin-bottom:28px}
  .signature{display:block;width:175px;height:26px;margin:18px 0 12px;background:linear-gradient(90deg,#d9d9d9,#e8e8e8);border-radius:3px}
  .badges{position:absolute;left:55px;top:922px;display:flex;gap:28px;align-items:flex-end}
  .badge{display:block;background:linear-gradient(180deg,var(--badge-gold),var(--badge-red));border-radius:4px;opacity:.75}
  .letterhead .badge.college{width:55px;height:75px}
  .letterhead .badge.association{width:78px;height:68px;background:linear-gradient(180deg,var(--badge-gold),#8a99b0)}
  .wave{position:absolute;left:0;bottom:0;width:100%}
  .site{position:absolute;color:#fff;font-size:12px;letter-spacing:.4px}
  .letterhead .site{right:75px;bottom:12px}
  .card{left:836px;width:312px;height:191px}
  .card-appointment{top:99px}
  .card-hartley{top:345px}
  .card-marrow{top:600px}
  .appt-title{position:absolute;top:25px;width:100%;text-align:center;font-weight:700;font-size:11px}
  .field{position:absolute;left:23px;right:23px;font-size:8px;display:flex;align-items:flex-end;gap:10px}
  .field .rule{flex:1;border-bottom:1px solid var(--line);height:9px;position:relative}
  .field .time{position:absolute;left:140px;bottom:0;font-size:8px}
  .card-appointment .brand-name{left:0;right:0;text-align:center;top:161px;font-size:9.5px}
  .card .brand-head{left:21px;top:33px;font-size:14px}
  .card .doctor{position:absolute;left:21px;top:86px;font-size:10.5px}
  .card .doctor .quals{font-size:8px}
  .card .role{position:absolute;left:21px;top:99px;font-size:8.5px;color:var(--navy)}
  .card .contact{position:absolute;right:19px;top:128px;font-size:8px;line-height:1.3}
  .card .icon{width:7px;height:7px}
  .card .badges{left:24px;top:131px;gap:14px}
  .card .badge.college{width:27px;height:38px}
  .card .badge.association{width:38px;height:35px;background:linear-gradient(180deg,var(--badge-gold),#8a99b0)}
  .card .site{right:19px;bottom:4px;font-size:8px}
</style>
</head>
<body>

<section class="sheet letterhead">
  <div class="brand-name">The Brightwater Joint Centre</div>
  <div class="practice-info">
    <div class="doctor">Dr Owen Hartley <span class="quals">MBBS, FRACS (Ortho)</span></div>
    <div class="doctor">Dr Lucien Marrow <span class="quals">MBBS, FRACS (Ortho)</span></div>
    <div class="contact">
      <div>02 65550737 <svg class="icon" viewBox="0 0 10 10"><path fill="var(--blue)" d="M2 0l2 2.5-1 1.2c.6 1.4 1.6 2.4 3 3l1.2-1L10 8l-1.2 1.8C4.5 9.6.4 5.5.2 1.2z"/></svg></div>
      <div>02 65550450 <svg class="icon" viewBox="0 0 10 10"><rect fill="var(--blue)" x="0" y="3" width="10" height="6" rx="1"/><rect fill="var(--blue)" x="2" y="0" width="6" height="3"/></svg></div>
      <div>info@brightwaterjoint.net.au <svg class="icon" viewBox="0 0 10 10"><rect x=".5" y="2" width="9" height="6.5" fill="none" stroke="var(--blue)"/><path d="M.5 2l4.5 4 4.5-4" fill="none" stroke="var(--blue)"/></svg></div>
    </div>
  </div>

  <article class="letter">
    <p class="date">November 12, 2019</p>
    <p class="recipient">Mr. Aaron Pell<br>President<br>Pell Holdings<br>111 Street Name, Suite#<br>City, State, 12345</p>
    <p class="salutation">Dear Mr. Aaron,</p>
    <p>Lorem ipsum dolor sit amet, consectetur adipiscing elit. Integer diam quam, egestas eu ultrices eu, suscipit ac sapien. Phasellus eu dui nisi. Nam et euismod diam, nec lobortis tortor. Donec et diam nulla. Aenean varius tincidunt convallis. Aliquam a tortor at lacus dictum aliquet. Nunc laoreet metus sapien, in scelerisque augue consectetur in.</p>
    <p>Fusce nec justo laoreet, egestas justo sed, aliquet sem. Pellentesque pharetra massa non orci bibendum semper. Pellentesque cursus eu lectus a consectetur. Nunc volutpat suscipit posuere. Vestibulum facilisis vel quam malesuada mattis. Nulla in mattis tellus. Maecenas tristique mauris vitae pharetra tincidunt. In ut ornare risus. Integer molestie vestibulum nisi, semper dapibus mi condimentum eu.</p>
    <p>Nullam sagittis elit libero, id fringilla est tincidunt eget. Donec in ipsum ultricies, consectetur quam vel, facilisis elit. Phasellus tincidunt congue risus vel luctus. Suspendisse ut mollis neque. Donec ornare orci in turpis vestibulum, in ultrices metus scelerisque. Pellentesque mattis mattis nunc, nec tincidunt lacus egestas id. Fusce facilisis sagittis neque sit amet vulputate. Aliquam ut eros lobortis tortor facilisis vehicula. Sed sed luctus leo, at laoreet sapien. Donec placerat adipiscing ligula non euismod. In lobortis pretium nisl id luctus.</p>
    <p>Integer gravida tincidunt nibh, scelerisque tincidunt turpis. Suspendisse potenti. Nunc hendrerit euismod lectus id elementum. Fusce vitae gravida velit, quis eleifend lectus. In imperdiet mauris eu dui viverra sagittis. Donec tempor dui diam, condimentum gravida lacus pretium a. Nullam fringilla augue quis arcu placerat scelerisque. Aliquam nec tincidunt augue, sit amet posuere ipsum.</p>
    <p style="margin-top:36px;margin-bottom:0">Sincerely Yours,</p>
    <span class="signature" role="img" aria-label="Handwritten signature of Martin Ellery"></span>
    <p style="margin:0">Martin Ellery<br>Managing Director</p>
  </article>

  <div class="badges">
    <span class="badge college" role="img" aria-label="Crestmoor Lindell College of Surgeons badge"></span>
    <span class="badge association" role="img" aria-label="Varenwood Bone Health Association badge"></span>
  </div>

  <svg class="wave" viewBox="0 0 728 60" height="60" preserveAspectRatio="none">
    <path d="M0 0C60 24 150 26 290 18S560 -2 680 12L728 22V60H0z" fill="var(--blue)"/>
    <path d="M0 16C80 34 180 34 320 24S580 14 728 24V60H0z" fill="#fff"/>
    <path d="M0 20C80 38 180 37 320 27S580 16 728 26V60H0z" fill="var(--navy)"/>
  </svg>
  <div class="site">www.brightwaterjoint.net.au</div>
</section>

<section class="sheet card card-appointment">
  <div class="appt-title">Next Appointment</div>
  <div class="field" style="top:66px">Name <span class="rule"></span></div>
  <div class="field" style="top:94px">Date <span class="rule"><span class="time">Time</span></span></div>
  <div class="field" style="top:122px">Note <span class="rule"></span></div>
  <div class="brand-name">The Brightwater Joint Centre</div>
</section>

<section class="sheet card card-hartley">
  <div class="brand-name brand-head">The Brightwater Joint Centre</div>
  <div class="doctor">Dr Owen Hartley <span class="quals">MBBS, FRACS (Ortho)</span></div>
  <div class="role">Orthopaedic Surgeon</div>
  <div class="badges">
    <span class="badge college" role="img" aria-label="Crestmoor Lindell College of Surgeons badge"></span>
    <span class="badge association" role="img" aria-label="Varenwood Bone Health Association badge"></span>
  </div>
  <div class="contact">
    <div>02 65550737 <svg class="icon" viewBox="0 0 10 10"><path fill="var(--blue)" d="M2 0l2 2.5-1 1.2c.6 1.4 1.6 2.4 3 3l1.2-1L10 8l-1.2 1.8C4.5 9.6.4 5.5.2 1.2z"/></svg></div>
    <div>02 65550450 <svg class="icon" viewBox="0 0 10 10"><rect fill="var(--blue)" x="0" y="3" width="10" height="6" rx="1"/><rect fill="var(--blue)" x="2" y="0" width="6" height="3"/></svg></div>
    <div>info@brightwaterjoint.net.au <svg class="icon" viewBox="0 0 10 10"><rect x=".5" y="2" width="9" height="6.5" fill="none" stroke="var(--blue)"/><path d="M.5 2l4.5 4 4.5-4" fill="none" stroke="var(--blue)"/></svg></div>
  </div>
  <svg class="wave" viewBox="0 0 312 26" height="26" preserveAspectRatio="none">
    <path d="M0 4C40 12 90 10 160 6S270 -2 312 8V26H0z" fill="var(--blue)"/>
    <path d="M0 10C40 18 100 16 170 11S280 6 312 11V26H0z" fill="#fff"/>
    <path d="M0 12C40 20 100 18 170 13S280 8 312 13V26H0z" fill="var(--navy)"/>
  </svg>
  <div class="site">www.brightwaterjoint.net.au</div>
</section>

<section class="sheet card card-marrow">
  <div class="brand-name brand-head">The Brightwater Joint Centre</div>
  <div class="doctor">Dr Lucien Marrow <span class="quals">MBBS, FRACS (Ortho)</span></div>
  <div class="role">Orthopaedic Surgeon</div>
  <div class="badges">
    <span class="badge college" role="img" aria-label="Crestmoor Lindell College of Surgeons badge"></span>
    <span class="badge association" role="img" aria-label="Varenwood Bone Health Association badge"></span>
  </div>
  <div class="contact">
    <div>02 65550737 <svg class="icon" viewBox="0 0 10 10"><path fill="var(--blue)" d="M2 0l2 2.5-1 1.2c.6 1.4 1.6 2.4 3 3l1.2-1L10 8l-1.2 1.8C4.5 9.6.4 5.5.2 1.2z"/></svg></div>
    <div>02 65550450 <svg class="icon" viewBox="0 0 10 10"><rect fill="var(--blue)" x="0" y="3" width="10" height="6" rx="1"/><rect fill="var(--blue)" x="2" y="0" width="6" height="3"/></svg></div>
    <div>info@brightwaterjoint.net.au <svg class="icon" viewBox="0 0 10 10"><rect x=".5" y="2" width="9" height="6.5" fill="none" stroke="var(--blue)"/><path d="M.5 2l4.5 4 4.5-4" fill="none" stroke="var(--blue)"/></svg></div>
  </div>
  <svg class="wave" viewBox="0 0 312 26" height="26" preserveAspectRatio="none">
    <path d="M0 4C40 12 90 10 160 6S270 -2 312 8V26H0z" fill="var(--blue)"/>
    <path d="M0 10C40 18 100 16 170 11S280 6 312 11V26H0z" fill="#fff"/>
    <path d="M0 12C40 20 100 18 170 13S280 8 312 13V26H0z" fill="var(--navy)"/>
  </svg>
  <div class="site">www.brightwaterjoint.net.au</div>
</section>

</body>
</html>
```